Redesign website for small print company

Vindurgata is a small printing company in Iceland mainly servicing Students, schools, etc. We are also doing all kind of other jobs, like business cards, book printing, brochure printing etc. We are also selling books online.
Our website is: www.vindurgata.is
What we are looking for is:
- Web Design (Uncoded - PSD layout only)
- Mobile friendly design, using our current color scheme: Red, green, yellow and light gray.
- Clean simple design
- Simple, light and easy to use.
- More menu Items/drop down
Industry/Entity Type
Digital Printing
Number of Pages Required
5+ page
Requirements
Must have
- Easy navigation
- Designed for mobile
- Current color scheme (see logo)
Nice to have
- Icon based products

```html
<!DOCTYPE html>
<html lang="is">
<head>
<meta charset="utf-8">
<title>Vindurgata – Prentþjónusta</title>
<link href="https://fonts.googleapis.com/css2?family=Open+Sans:ital,wght@0,400;0,600;0,700;0,800;1,400&display=swap" rel="stylesheet">
<style>
:root{
  --red:#e2282a;
  --green:#1d5a2c;
  --green-dark:#15502a;
  --blue:#1f6fb4;
  --yellow:#f8d53a;
  --light:#f1f1f1;
  --line:#dcdcdc;
  --text:#333;
  --muted:#666;
  --black:#0c0c0c;
}
*{box-sizing:border-box;margin:0;padding:0}
html,body{width:1200px;height:3020px;overflow:hidden}
body{font-family:"Open Sans",Arial,sans-serif;color:var(--text);background:#fff;position:relative}
a{color:inherit;text-decoration:none}
.abs{position:absolute}

/* header */
.site-header{position:absolute;left:0;top:0;width:1200px;height:118px;background:#fff}
.brand{left:75px;top:32px;display:flex;align-items:center;gap:14px}
.brand-mark{width:44px;height:44px;background:var(--red)}
.brand-name{font-size:34px;font-weight:800;color:#222;letter-spacing:.5px}
.top-links{right:75px;top:20px;font-size:14px;color:#333;word-spacing:2px}
.phone{left:604px;top:70px;display:flex;align-items:center;gap:8px;color:var(--red);font-weight:700;font-size:21px}
.search{left:739px;top:60px;width:387px;height:43px;border:1px solid #cfcfcf;display:flex;font-size:13px}
.search .cat{width:125px;border-right:1px solid #cfcfcf;display:flex;align-items:center;justify-content:space-between;padding:0 10px;background:#f5f5f5;color:#444}
.search .field{flex:1;display:flex;align-items:center;padding:0 10px;color:#666}
.search .go{width:36px;display:flex;align-items:center;justify-content:center}

/* nav */
.main-nav{position:absolute;left:0;top:118px;width:1200px;height:50px;background:var(--black);color:#fff;font-size:13px;font-weight:700}
.nav-item{position:absolute;top:17px;white-space:nowrap}
.cart{position:absolute;right:75px;top:16px;display:flex;align-items:center;gap:10px;font-weight:400;white-space:nowrap}
.dropdown{position:absolute;left:133px;top:168px;width:226px;height:138px;background:var(--yellow);z-index:5;padding:18px 18px;font-size:14px;color:#222;line-height:31px}

/* hero */
.hero{position:absolute;left:0;top:168px;width:1200px;height:472px;background:linear-gradient(90deg,#f2f2f2 0%,#e8e8e8 60%,#f0f0f0 100%)}
.hero-art{left:560px;top:8px;width:570px;height:455px;background:linear-gradient(135deg,#f3f3f3,#d9e1ee 40%,#e8c7e8 65%,#f5f5f5);border-radius:4px}
.hero-title{left:73px;top:122px;color:var(--green);font-size:56px;line-height:60px;font-weight:400;letter-spacing:.5px;z-index:2}
.hero-sub{left:73px;top:244px;font-size:26px;color:#111;white-space:nowrap;z-index:2}
.btn-red{left:75px;top:305px;width:180px;height:47px;background:var(--red);color:#fff;font-weight:700;font-size:15px;display:flex;align-items:center;justify-content:center}
.dots{left:75px;top:423px;display:flex;gap:9px}
.dots i{width:10px;height:10px;border-radius:50%;background:#777;display:block}
.dots i:first-child{background:var(--red)}

/* sections */
.section-title{font-size:23px;font-weight:700;color:#222}
.categories{position:absolute;left:0;top:640px;width:1200px;height:443px;background:#fff}
.cat-card{position:absolute;top:93px;width:242px;height:242px;background:linear-gradient(180deg,#f4f4f4,#e9e9e9);text-align:center}
.cat-card svg{margin-top:38px}
.cat-card h3{font-size:23px;color:var(--green);font-weight:700;margin-top:14px}
.cat-card p{font-size:14px;color:#555;line-height:22px;margin-top:6px}
.btn-outline{left:498px;top:369px;width:204px;height:36px;border:1px solid var(--red);color:var(--red);font-size:14px;font-weight:600;display:flex;align-items:center;justify-content:center}

.products{position:absolute;left:0;top:1083px;width:1200px;height:481px;background:var(--light)}
.books{position:absolute;left:0;top:1564px;width:1200px;height:465px;background:#fff}
.arrows{right:75px;top:45px;display:flex;gap:12px}
.arrows span{width:30px;height:30px;border:1px solid var(--red);display:flex;align-items:center;justify-content:center;background:#fff}
.p-card{position:absolute;top:101px;width:244px;height:318px;background:#fff;border:1px solid var(--line);text-align:center}
.p-card .heart{position:absolute;right:12px;top:10px}
.p-img{margin:22px auto 0;width:196px;height:140px;background:linear-gradient(135deg,#d8dde6,#b9c2d0)}
.p-card h4{font-size:14px;font-weight:700;color:var(--blue);margin-top:18px}
.p-card p{font-size:14px;color:#444;line-height:22px;margin-top:6px}
.p-card .price{font-size:16px;font-weight:700;color:var(--green-dark);margin-top:4px}
.p-card .acts{display:flex;justify-content:center;gap:22px;margin-top:9px}

/* about */
.about{position:absolute;left:0;top:2029px;width:1200px;height:411px;background:linear-gradient(90deg,#e3252a 0%,#a8342a 35%,#5a3c22 60%,#1b5a2c 100%);color:#fff}
.about h2{left:75px;top:45px;font-size:23px;font-weight:700}
.about p{left:75px;top:100px;width:520px;font-size:14px;line-height:26px}
.btn-yellow{left:75px;top:318px;width:152px;height:44px;background:var(--yellow);color:var(--red);font-weight:700;font-size:15px;display:flex;align-items:center;justify-content:center}
.about-photo{left:615px;top:52px;width:512px;height:306px;border:5px solid #fff;background:linear-gradient(135deg,#7c8a96,#c4ccd3 50%,#6f8a70)}

/* perks */
.perks{position:absolute;left:0;top:2440px;width:1200px;height:207px;background:#fff}
.perk{position:absolute;top:43px;width:330px;height:131px;border:1px solid var(--red);display:flex;align-items:center;padding-left:28px;gap:26px}
.perk h3{color:var(--red);font-size:21px;font-weight:700}
.perk p{font-size:13px;font-style:italic;color:#444;line-height:20px;margin-top:4px}

/* footer */
.site-footer{position:absolute;left:0;top:2647px;width:1200px;height:306px;background:var(--light)}
.f-col{position:absolute;top:48px}
.f-col h5{font-size:13px;font-weight:700;color:var(--green-dark);margin-bottom:12px}
.f-col li{list-style:none;font-size:13px;color:#444;line-height:31px}
.subscribe{display:flex;width:270px;height:44px;margin-top:4px}
.subscribe .in{flex:1;background:#fff;border:1px solid #ccc;font-size:14px;color:#555;display:flex;align-items:center;padding-left:14px}
.subscribe .go{width:52px;background:var(--yellow);color:var(--red);font-weight:800;display:flex;align-items:center;justify-content:center;font-size:17px}
.social{display:flex;gap:18px;margin-top:8px}
.social i{display:block;width:16px;height:16px;background:#333}
.copyright{position:absolute;left:0;top:2953px;width:1200px;height:67px;background:#dedede;font-size:12px;color:#333;display:flex;align-items:center;justify-content:center}
</style>
</head>
<body>

<header class="site-header">
  <div class="abs brand"><span class="brand-mark"></span><span class="brand-name">VINDURGATA</span></div>
  <div class="abs top-links">Login &nbsp;/&nbsp; Register &nbsp;/&nbsp; My Account &nbsp;/&nbsp; Wishlist &nbsp;/&nbsp; FAQ</div>
  <div class="abs phone">
    <svg width="16" height="16" viewBox="0 0 24 24"><path fill="#e2282a" d="M6.6 10.8a15 15 0 0 0 6.6 6.6l2.2-2.2c.3-.3.7-.4 1-.2 1.1.4 2.3.6 3.6.6.6 0 1 .4 1 1V20c0 .6-.4 1-1 1A17 17 0 0 1 3 4c0-.6.4-1 1-1h3.5c.6 0 1 .4 1 1 0 1.3.2 2.5.6 3.6.1.3 0 .7-.2 1z"/></svg>
    555 0192
  </div>
  <div class="abs search">
    <div class="cat">By Categories <span>⌄</span></div>
    <div class="field">Search..</div>
    <div class="go"><svg width="15" height="15" viewBox="0 0 24 24"><circle cx="10" cy="10" r="7" fill="none" stroke="#1d5a2c" stroke-width="3"/><path d="M15 15l6 6" stroke="#1d5a2c" stroke-width="3"/></svg></div>
  </div>
</header>

<nav class="main-nav">
  <span class="nav-item" style="left:78px">HOME</span>
  <span class="nav-item" style="left:165px">PRODUCTS &nbsp;⌄</span>
  <span class="nav-item" style="left:296px">ABOUT US</span>
  <span class="nav-item" style="left:411px">SERVICES</span>
  <span class="nav-item" style="left:519px">CONTACT US</span>
  <div class="cart">
    <svg width="18" height="16" viewBox="0 0 24 22"><path fill="#f8d53a" d="M0 1h4l1 3h19l-3 10H7L3 3H0z"/><circle cx="9" cy="19" r="2" fill="#f8d53a"/><circle cx="19" cy="19" r="2" fill="#f8d53a"/></svg>
    <span>My Cart <b>(0)</b></span>
  </div>
</nav>

<div class="dropdown">
  <div>Business Cards</div>
  <div>Book printing</div>
  <div>Brochure Printing</div>
  <div>Leaflet</div>
</div>

<section class="hero">
  <div class="abs hero-art" role="img" aria-label="Colourful folded brochure and roll-up banner mockup"></div>
  <h1 class="abs hero-title">WELCOME TO<br>VINDURGATA</h1>
  <p class="abs hero-sub">Lorem ipsum dolor sit amet, consectetur..</p>
  <a class="abs btn-red">SHOP NOW</a>
  <div class="abs dots"><i></i><i></i><i></i><i></i></div>
</section>

<section class="categories">
  <h2 class="section-title" style="position:absolute;top:38px;width:100%;text-align:center">CATEGORIES</h2>
  <div class="cat-card" style="left:75px">
    <svg width="50" height="56" viewBox="0 0 50 56"><path d="M4 2h30l12 12v40H4z" fill="#c8262b"/><path d="M34 2v12h12" fill="#8e1b1f"/><rect x="12" y="22" width="26" height="3" fill="#fff"/><rect x="12" y="30" width="26" height="3" fill="#fff"/><rect x="12" y="38" width="18" height="3" fill="#fff"/></svg>
    <h3>Essays</h3><p>Lorem ipsum dolor sit amet,<br>consectetur adipisc...</p>
  </div>
  <div class="cat-card" style="left:344px">
    <svg width="74" height="56" viewBox="0 0 74 56"><rect x="2" y="8" width="70" height="44" rx="4" fill="#c8262b"/><rect x="2" y="8" width="70" height="10" fill="#8e1b1f"/><circle cx="20" cy="32" r="7" fill="#fff"/><rect x="34" y="26" width="30" height="4" fill="#fff"/><rect x="34" y="34" width="24" height="4" fill="#fff"/></svg>
    <h3>Business Cards</h3><p>Lorem ipsum dolor sit amet,<br>consectetur adipisc...</p>
  </div>
  <div class="cat-card" style="left:614px">
    <svg width="60" height="56" viewBox="0 0 60 56"><path d="M2 10l14-8v46L2 54z" fill="#1d5a2c"/><path d="M16 2l14 8v46L16 48z" fill="#c8262b"/><path d="M30 10l14-8v46l-14 8z" fill="#1d5a2c"/><path d="M44 2l14 8v46l-14-8z" fill="#c8262b"/></svg>
    <h3>Leaflet</h3><p>Lorem ipsum dolor sit amet,<br>consectetur adipisc...</p>
  </div>
  <div class="cat-card" style="left:883px">
    <svg width="54" height="56" viewBox="0 0 54 56"><path d="M14 4h36l-10 40H4z" fill="#c8262b"/><path d="M4 44h36v8H4z" fill="#1d5a2c"/><path d="M40 44l10-40v8l-10 40z" fill="#8e1b1f"/></svg>
    <h3>Textbooks</h3><p>Lorem ipsum dolor sit amet,<br>consectetur adipisc...</p>
  </div>
  <a class="abs btn-outline">VIEW ALL CATEGORIES</a>
</section>

<section class="products">
  <h2 class="section-title abs" style="left:75px;top:47px">FEATURED PRODUCTS</h2>
  <div class="abs arrows"><span><svg width="8" height="12" viewBox="0 0 8 12"><path d="M7 1L2 6l5 5" fill="none" stroke="#333" stroke-width="2"/></svg></span><span><svg width="8" height="12" viewBox="0 0 8 12"><path d="M1 1l5 5-5 5" fill="none" stroke="#333" stroke-width="2"/></svg></span></div>
  <article class="p-card" style="left:75px"><svg class="heart" width="18" height="16" viewBox="0 0 24 22"><path d="M12 20S2 14 2 7a5 5 0 0 1 10-1 5 5 0 0 1 10 1c0 7-10 13-10 13z" fill="none" stroke="#e2282a" stroke-width="2.4"/></svg><div class="p-img" role="img" aria-label="Printed stationery set"></div><h4>DONEC HENDRERIT</h4><p>Nam laoreet lacus pellentesque<br>metus &nbsp;vehicula molestie</p><div class="price">$00.00</div><div class="acts"><svg width="14" height="13" viewBox="0 0 24 22"><path fill="#333" d="M0 1h4l1 3h19l-3 10H7L3 3H0z"/><circle cx="9" cy="19" r="2" fill="#333"/><circle cx="19" cy="19" r="2" fill="#333"/></svg><svg width="16" height="12" viewBox="0 0 24 16"><path d="M12 1C6 1 2 8 2 8s4 7 10 7 10-7 10-7-4-7-10-7z" fill="#333"/><circle cx="12" cy="8" r="3" fill="#fff"/></svg><svg width="14" height="14" viewBox="0 0 24 24"><circle cx="12" cy="12" r="11" fill="#333"/><rect x="10.5" y="10" width="3" height="8" fill="#fff"/><circle cx="12" cy="6.5" r="1.8" fill="#fff"/></svg></div></article>
  <article class="p-card" style="left:344px"><svg class="heart" width="18" height="16" viewBox="0 0 24 22"><path d="M12 20S2 14 2 7a5 5 0 0 1 10-1 5 5 0 0 1 10 1c0 7-10 13-10 13z" fill="none" stroke="#e2282a" stroke-width="2.4"/></svg><div class="p-img" role="img" aria-label="Folded greeting card" style="background:linear-gradient(135deg,#e4e9f2,#9fb2d6)"></div><h4>DONEC HENDRERIT</h4><p>Nam laoreet lacus pellentesque<br>metus &nbsp;vehicula molestie</p><div class="price">$00.00</div><div class="acts"><svg width="14" height="13" viewBox="0 0 24 22"><path fill="#333" d="M0 1h4l1 3h19l-3 10H7L3 3H0z"/><circle cx="9" cy="19" r="2" fill="#333"/><circle cx="19" cy="19" r="2" fill="#333"/></svg><svg width="16" height="12" viewBox="0 0 24 16"><path d="M12 1C6 1 2 8 2 8s4 7 10 7 10-7 10-7-4-7-10-7z" fill="#333"/><circle cx="12" cy="8" r="3" fill="#fff"/></svg><svg width="14" height="14" viewBox="0 0 24 24"><circle cx="12" cy="12" r="11" fill="#333"/><rect x="10.5" y="10" width="3" height="8" fill="#fff"/><circle cx="12" cy="6.5" r="1.8" fill="#fff"/></svg></div></article>
  <article class="p-card" style="left:614px"><svg class="heart" width="18" height="16" viewBox="0 0 24 22"><path d="M12 20S2 14 2 7a5 5 0 0 1 10-1 5 5 0 0 1 10 1c0 7-10 13-10 13z" fill="none" stroke="#e2282a" stroke-width="2.4"/></svg><div class="p-img" role="img" aria-label="Assorted printed brochures and flyers" style="background:linear-gradient(135deg,#3a3f4a,#6f8fb0 50%,#c8a75a)"></div><h4>DONEC HENDRERIT</h4><p>Nam laoreet lacus pellentesque<br>metus &nbsp;vehicula molestie</p><div class="price">$00.00</div><div class="acts"><svg width="14" height="13" viewBox="0 0 24 22"><path fill="#333" d="M0 1h4l1 3h19l-3 10H7L3 3H0z"/><circle cx="9" cy="19" r="2" fill="#333"/><circle cx="19" cy="19" r="2" fill="#333"/></svg><svg width="16" height="12" viewBox="0 0 24 16"><path d="M12 1C6 1 2 8 2 8s4 7 10 7 10-7 10-7-4-7-10-7z" fill="#333"/><circle cx="12" cy="8" r="3" fill="#fff"/></svg><svg width="14" height="14" viewBox="0 0 24 24"><circle cx="12" cy="12" r="11" fill="#333"/><rect x="10.5" y="10" width="3" height="8" fill="#fff"/><circle cx="12" cy="6.5" r="1.8" fill="#fff"/></svg></div></article>
  <article class="p-card" style="left:883px"><svg class="heart" width="18" height="16" viewBox="0 0 24 22"><path d="M12 20S2 14 2 7a5 5 0 0 1 10-1 5 5 0 0 1 10 1c0 7-10 13-10 13z" fill="none" stroke="#e2282a" stroke-width="2.4"/></svg><div class="p-img" role="img" aria-label="Rolled printed poster" style="background:linear-gradient(135deg,#f2f2f2,#2a2a2a 55%,#e5e5e5)"></div><h4>DONEC HENDRERIT</h4><p>Nam laoreet lacus pellentesque<br>metus &nbsp;vehicula molestie</p><div class="price">$00.00</div><div class="acts"><svg width="14" height="13" viewBox="0 0 24 22"><path fill="#333" d="M0 1h4l1 3h19l-3 10H7L3 3H0z"/><circle cx="9" cy="19" r="2" fill="#333"/><circle cx="19" cy="19" r="2" fill="#333"/></svg><svg width="16" height="12" viewBox="0 0 24 16"><path d="M12 1C6 1 2 8 2 8s4 7 10 7 10-7 10-7-4-7-10-7z" fill="#333"/><circle cx="12" cy="8" r="3" fill="#fff"/></svg><svg width="14" height="14" viewBox="0 0 24 24"><circle cx="12" cy="12" r="11" fill="#333"/><rect x="10.5" y="10" width="3" height="8" fill="#fff"/><circle cx="12" cy="6.5" r="1.8" fill="#fff"/></svg></div></article>
</section>

<section class="books">
  <h2 class="section-title abs" style="left:75px;top:47px">FEATURED BOOKS</h2>
  <div class="abs arrows"><span><svg width="8" height="12" viewBox="0 0 8 12"><path d="M7 1L2 6l5 5" fill="none" stroke="#333" stroke-width="2"/></svg></span><span><svg width="8" height="12" viewBox="0 0 8 12"><path d="M1 1l5 5-5 5" fill="none" stroke="#333" stroke-width="2"/></svg></span></div>
  <article class="p-card" style="left:75px"><svg class="heart" width="18" height="16" viewBox="0 0 24 22"><path d="M12 20S2 14 2 7a5 5 0 0 1 10-1 5 5 0 0 1 10 1c0 7-10 13-10 13z" fill="none" stroke="#e2282a" stroke-width="2.4"/></svg><div class="p-img" role="img" aria-label="Book cover" style="width:90px;background:linear-gradient(135deg,#a07c2a,#6b5220)"></div><h4>DONEC HENDRERIT</h4><p>Nam laoreet lacus pellentesque<br>metus &nbsp;vehicula molestie</p><div class="price">$00.00</div><div class="acts"><svg width="14" height="13" viewBox="0 0 24 22"><path fill="#333" d="M0 1h4l1 3h19l-3 10H7L3 3H0z"/><circle cx="9" cy="19" r="2" fill="#333"/><circle cx="19" cy="19" r="2" fill="#333"/></svg><svg width="16" height="12" viewBox="0 0 24 16"><path d="M12 1C6 1 2 8 2 8s4 7 10 7 10-7 10-7-4-7-10-7z" fill="#333"/><circle cx="12" cy="8" r="3" fill="#fff"/></svg><svg width="14" height="14" viewBox="0 0 24 24"><circle cx="12" cy="12" r="11" fill="#333"/><rect x="10.5" y="10" width="3" height="8" fill="#fff"/><circle cx="12" cy="6.5" r="1.8" fill="#fff"/></svg></div></article>
  <article class="p-card" style="left:344px"><svg class="heart" width="18" height="16" viewBox="0 0 24 22"><path d="M12 20S2 14 2 7a5 5 0 0 1 10-1 5 5 0 0 1 10 1c0 7-10 13-10 13z" fill="none" stroke="#e2282a" stroke-width="2.4"/></svg><div class="p-img" role="img" aria-label="Book cover" style="width:100px;background:linear-gradient(160deg,#e8157f 0 25%,#f4f4f4 25%)"></div><h4>DONEC HENDRERIT</h4><p>Nam laoreet lacus pellentesque<br>metus &nbsp;vehicula molestie</p><div class="price">$00.00</div><div class="acts"><svg width="14" height="13" viewBox="0 0 24 22"><path fill="#333" d="M0 1h4l1 3h19l-3 10H7L3 3H0z"/><circle cx="9" cy="19" r="2" fill="#333"/><circle cx="19" cy="19" r="2" fill="#333"/></svg><svg width="16" height="12" viewBox="0 0 24 16"><path d="M12 1C6 1 2 8 2 8s4 7 10 7 10-7 10-7-4-7-10-7z" fill="#333"/><circle cx="12" cy="8" r="3" fill="#fff"/></svg><svg width="14" height="14" viewBox="0 0 24 24"><circle cx="12" cy="12" r="11" fill="#333"/><rect x="10.5" y="10" width="3" height="8" fill="#fff"/><circle cx="12" cy="6.5" r="1.8" fill="#fff"/></svg></div></article>
  <article class="p-card" style="left:614px"><svg class="heart" width="18" height="16" viewBox="0 0 24 22"><path d="M12 20S2 14 2 7a5 5 0 0 1 10-1 5 5 0 0 1 10 1c0 7-10 13-10 13z" fill="none" stroke="#e2282a" stroke-width="2.4"/></svg><div class="p-img" role="img" aria-label="Book cover" style="width:80px;background:linear-gradient(180deg,#f4f4f4 0 35%,#2c4a3a 35% 65%,#f4f4f4 65%)"></div><h4>DONEC HENDRERIT</h4><p>Nam laoreet lacus pellentesque<br>metus &nbsp;vehicula molestie</p><div class="price">$00.00</div><div class="acts"><svg width="14" height="13" viewBox="0 0 24 22"><path fill="#333" d="M0 1h4l1 3h19l-3 10H7L3 3H0z"/><circle cx="9" cy="19" r="2" fill="#333"/><circle cx="19" cy="19" r="2" fill="#333"/></svg><svg width="16" height="12" viewBox="0 0 24 16"><path d="M12 1C6 1 2 8 2 8s4 7 10 7 10-7 10-7-4-7-10-7z" fill="#333"/><circle cx="12" cy="8" r="3" fill="#fff"/></svg><svg width="14" height="14" viewBox="0 0 24 24"><circle cx="12" cy="12" r="11" fill="#333"/><rect x="10.5" y="10" width="3" height="8" fill="#fff"/><circle cx="12" cy="6.5" r="1.8" fill="#fff"/></svg></div></article>
  <article class="p-card" style="left:883px"><svg class="heart" width="18" height="16" viewBox="0 0 24 22"><path d="M12 20S2 14 2 7a5 5 0 0 1 10-1 5 5 0 0 1 10 1c0 7-10 13-10 13z" fill="none" stroke="#e2282a" stroke-width="2.4"/></svg><div class="p-img" role="img" aria-label="Book cover" style="width:80px;background:linear-gradient(180deg,#f4f4f4 0 50%,#d7262a 50% 62%,#f4f4f4 62%)"></div><h4>DONEC HENDRERIT</h4><p>Nam laoreet lacus pellentesque<br>metus &nbsp;vehicula molestie</p><div class="price">$00.00</div><div class="acts"><svg width="14" height="13" viewBox="0 0 24 22"><path fill="#333" d="M0 1h4l1 3h19l-3 10H7L3 3H0z"/><circle cx="9" cy="19" r="2" fill="#333"/><circle cx="19" cy="19" r="2" fill="#333"/></svg><svg width="16" height="12" viewBox="0 0 24 16"><path d="M12 1C6 1 2 8 2 8s4 7 10 7 10-7 10-7-4-7-10-7z" fill="#333"/><circle cx="12" cy="8" r="3" fill="#fff"/></svg><svg width="14" height="14" viewBox="0 0 24 24"><circle cx="12" cy="12" r="11" fill="#333"/><rect x="10.5" y="10" width="3" height="8" fill="#fff"/><circle cx="12" cy="6.5" r="1.8" fill="#fff"/></svg></div></article>
</section>

<section class="about">
  <h2 class="abs">ABOUT OUR COMPANY</h2>
  <p class="abs">Vindurgata er fyrirtæki staðsett á háskólasvæðinu sem hefur sérhæft sig í að þjónusta skólafólk, ásamt því að sinna allri almennri prentun fyrir almenning. Vindurgata gefur út greinasöfn og frumsamdar kennslubækur fyrir námskeið, prentar lokaritgerðir fyrir nema, auk þess að vinna við ótalinn fjölda smærri verka fyrir nemendur, kennara og stofnanir. Má þar nefna bæklinga, skýrslur, spurningalista, nafnspjöld, bækur, OCR skönnun og fleira.</p>
  <a class="abs btn-yellow">READ MORE</a>
  <div class="abs about-photo" role="img" aria-label="Printed books moving along a press conveyor"></div>
</section>

<section class="perks">
  <div class="perk" style="left:75px">
    <svg width="62" height="42" viewBox="0 0 62 42"><rect x="0" y="4" width="36" height="26" fill="#c8262b"/><path d="M36 12h14l10 10v8H36z" fill="#c8262b"/><rect x="40" y="15" width="9" height="7" fill="#fff"/><circle cx="12" cy="34" r="6" fill="#333"/><circle cx="48" cy="34" r="6" fill="#333"/></svg>
    <div><h3>FREE SHIPPING</h3><p>Vestibulum ante ipsum primis<br>in faucibus orci luctus</p></div>
  </div>
  <div class="perk" style="left:435px">
    <svg width="40" height="60" viewBox="0 0 40 60"><text x="20" y="50" text-anchor="middle" font-family="Open Sans, sans-serif" font-weight="800" font-size="56" fill="#1d5a2c">$</text></svg>
    <div><h3>20% OFF</h3><p>Vestibulum ante ipsum primis<br>in faucibus orci luctus</p></div>
  </div>
  <div class="perk" style="left:795px">
    <svg width="56" height="44" viewBox="0 0 56 44"><path d="M22 2L2 18l20 16V24c14 0 24 4 32 18 0-18-10-30-32-30z" fill="#8e1b1f"/></svg>
    <div><h3>EASY RETURN</h3><p>Vestibulum ante ipsum primis<br>in faucibus orci luctus</p></div>
  </div>
</section>

<footer class="site-footer">
  <div class="f-col" style="left:75px"><h5>QUICK LINKS</h5><ul><li>Home</li><li>Products</li><li>About Us</li><li>Services</li><li>Contact Us</li></ul></div>
  <div class="f-col" style="left:344px"><h5>PRODUCTS</h5><ul><li>Essays</li><li>Business cards</li><li>Leaflet</li><li>Bookprinting</li><li>Posters</li><li>Textbooks</li></ul></div>
  <div class="f-col" style="left:630px"><h5>MY ACCOUNT</h5><ul><li>Log In</li><li>My Account</li><li>Register</li><li>Return Policy</li><li>Wishlist</li></ul></div>
  <div class="f-col" style="left:856px"><h5>EMAIL SUBSCRIBE</h5>
    <div class="subscribe"><div class="in">Enter Email Address</div><div class="go">GO</div></div>
    <h5 style="margin-top:22px">FOLLOW US</h5>
    <div class="social" aria-label="Social links"><i></i><i></i><i></i><i></i><i></i><i></i></div>
  </div>
</footer>
<div class="copyright">Copyright © 2018 &nbsp;Company Name. All Right Reserved</div>

</body>
</html>
```